Business card design needed

My business is in Matchmaking. My objective is to find the most compatible partner for my clients....basically I'm in the love and happiness industry bringing two people together for a lasting loving relationship.

I envision the design to be something with 2 people who are in love looking happy or even a silhouette.....I don't really know, I'm open to ideas.....maybe no picture at all, but I want it to be classy :-)

I do have a logo which I will upload. You can also go to my website to give you an idea on the colours and the design if that helps, however the website is not finished yet, it should be up by today or tomorrow. If the website has a heart with swirls on the upper left hand corner, that is the old website, please ignore that one. The one that will be up shortly has a picture frame on the home page with my logo that will be in the file I will upload on this page.

Target Market(s)

There are three categories: Over 45, Asian and Western and same sex, but would be able to afford to hire a matchmaker

Contact Information for Business Card

The Tidewell Bureau
Helping You Find The "One"
Mavis Ellery
Matchmaker
0492 517 264
info@tidewellbureau.com.au
www.tidewellbureau.com.au

```html
<!DOCTYPE html>
<html lang="en">
<head>
<meta charset="utf-8">
<title>The Tidewell Bureau – Business Card</title>
<link rel="stylesheet" href="https://fonts.googleapis.com/css2?family=Source+Sans+3:wght@600;700&display=swap">
<style>
  :root {
    --cream: #fffbdb;
    --cream-text: #fff8d8;
    --plum: #8a6a74;
    --plum-dark: #7a5c66;
    --slate-teal: #8fa7a8;
    --photo-light: #9a9a9a;
    --photo-dark: #1e1e1e;
    --page: #ffffff;
  }
  * { margin: 0; padding: 0; box-sizing: border-box; }
  html, body {
    width: 1200px;
    height: 693px;
    overflow: hidden;
    background: var(--page);
  }
  .card {
    position: relative;
    width: 1200px;
    height: 693px;
    background: var(--cream);
    font-family: "Source Sans 3", "Myriad Pro", Arial, sans-serif;
    overflow: hidden;
  }
  .card__photo {
    position: absolute;
    left: 0; top: 0;
    width: 466px;
    height: 693px;
    background: radial-gradient(ellipse at 40% 55%, var(--photo-light) 0%, #5e5e5e 45%, var(--photo-dark) 100%);
  }
  .card__divider {
    position: absolute;
    left: 466px; top: 0;
    width: 4px;
    height: 693px;
    background: var(--slate-teal);
  }
  .brand {
    position: absolute;
    left: 470px; top: 0;
    width: 730px;
    height: 403px;
    text-align: center;
  }
  .brand__mark {
    position: absolute;
    left: 50%; top: 78px;
    width: 118px; height: 118px;
    margin-left: -59px;
    border-radius: 50%;
    background: var(--plum);
    opacity: 0.85;
  }
  .brand__name {
    position: absolute;
    left: 0; right: 0; top: 228px;
    font-size: 46px;
    font-weight: 600;
    color: var(--plum);
    letter-spacing: 0.5px;
  }
  .brand__tagline {
    position: absolute;
    left: 0; right: 0; top: 312px;
    font-size: 34px;
    font-weight: 700;
    color: var(--plum);
    letter-spacing: -1.2px;
  }
  .contact {
    position: absolute;
    left: 470px; top: 403px;
    width: 730px;
    height: 290px;
    background: var(--plum);
    border-top: 2px solid var(--plum-dark);
    color: var(--cream-text);
    padding-left: 56px;
  }
  .contact__name {
    margin-top: 14px;
    font-size: 52px;
    font-weight: 700;
    line-height: 1.05;
    letter-spacing: -0.5px;
  }
  .contact__role {
    font-size: 30px;
    font-weight: 700;
    line-height: 1.15;
    letter-spacing: -0.5px;
  }
  .contact__lines {
    margin-top: 22px;
    list-style: none;
    font-size: 34px;
    font-weight: 700;
    line-height: 1.08;
    letter-spacing: -0.8px;
  }
</style>
</head>
<body>
  <main class="card">
    <div class="card__photo" role="img" aria-label="Black and white photograph of a couple's clasped hands, one wearing an engagement ring"></div>
    <div class="card__divider"></div>

    <section class="brand">
      <div class="brand__mark"></div>
      <div class="brand__name">The Tidewell Bureau</div>
      <div class="brand__tagline">Helping You Find The "One"</div>
    </section>

    <section class="contact">
      <h1 class="contact__name">Mavis Ellery</h1>
      <p class="contact__role">Matchmaker</p>
      <ul class="contact__lines">
        <li class="contact__phone">Tel. 0492 517 264</li>
        <li class="contact__email">mavis@tidewellbureau.com.au</li>
        <li class="contact__web">www.tidewellbureau.com.au</li>
      </ul>
    </section>
  </main>
</body>
</html>
```